We need a card and logo design for a new business based in Dallas Texas called Stonemarsh Financial LLC.

We provide bridge loans.We offer pay day loans,title loans and check cashing.Our products are emmergency loans that help borrowers meet short term liquidity needs until the next pay check.

The final design should communicate,professionalism,Sophistication and friendliness to our customers.Use the color Blue as much as possible and another eye catching color if possible.We will consider a profesional looking knight logo with the color Blue in it.Please design a full corporate identity.

```html
<!DOCTYPE html>
<html lang="en">
<head>
<meta charset="utf-8">
<title>Stonemarsh Financial LLC – Business Card</title>
<link rel="stylesheet" href="https://fonts.googleapis.com/css2?family=Cinzel:wght@500&family=Open+Sans:wght@400;600;700&display=swap">
<style>
  :root {
    --stage: #2f2b29;
    --card-white: #f1f1f1;
    --card-white-edge: #e2e2e2;
    --brand-blue: #2a4f9f;
    --ink: #111111;
    --back-blue-centre: #0d4ea3;
    --back-blue-edge: #253f80;
    --white: #ffffff;
    --label: #bdbdbd;
  }
  * { margin: 0; padding: 0; box-sizing: border-box; }
  html, body { width: 1000px; height: 1200px; overflow: hidden; }
  body {
    background: var(--stage);
    font-family: "Open Sans", Arial, sans-serif;
    position: relative;
  }
  .card {
    position: absolute;
    width: 723px;
    height: 423px;
    box-shadow: 0 3px 10px rgba(0,0,0,0.45);
  }
  .card--front {
    left: 140px; top: 119px;
    background: linear-gradient(160deg, var(--card-white) 0%, var(--card-white-edge) 100%);
  }
  .card--back {
    left: 125px; top: 638px;
    background: radial-gradient(ellipse 60% 65% at 50% 30%, var(--back-blue-centre) 0%, var(--back-blue-edge) 100%);
  }
  .side-label {
    position: absolute;
    color: var(--label);
    font-family: Arial, sans-serif;
    font-size: 20px;
  }
  .side-label--front { left: 139px; top: 590px; }
  .side-label--back { left: 799px; top: 1116px; }

  .holder { position: absolute; right: 36px; top: 44px; text-align: right; }
  .holder__name {
    font-family: "Cinzel", Georgia, serif;
    font-weight: 500;
    font-size: 26px;
    color: var(--brand-blue);
    line-height: 1;
  }
  .holder__title {
    font-weight: 600;
    font-size: 18px;
    color: var(--ink);
    margin-top: 4px;
  }

  .brand-name {
    position: absolute;
    left: 0; right: 0;
    text-align: center;
    font-weight: 700;
    font-size: 30px;
    letter-spacing: 0.5px;
    white-space: nowrap;
  }
  .card--front .brand-name { top: 204px; color: var(--brand-blue); }
  .card--back .brand-name { top: 180px; color: var(--white); font-size: 34px; }

  .rule { position: absolute; }
  .card--front .rule--under { left: 270px; top: 257px; width: 183px; height: 2px; background: var(--ink); }
  .card--front .rule--divider { left: 360px; top: 257px; width: 2px; height: 82px; background: var(--ink); }
  .card--back .rule--under { left: 256px; top: 256px; width: 211px; height: 2px; background: var(--white); }

  .contact { position: absolute; font-size: 16px; line-height: 22px; color: var(--ink); }
  .contact__row { display: flex; margin-bottom: 9px; }
  .contact__label { color: var(--brand-blue); font-weight: 600; }
  .contact--left { left: 51px; top: 275px; }
  .contact--left .contact__label { width: 62px; }
  .contact--right { left: 393px; top: 275px; }
  .contact--right .contact__label { width: 75px; }

  .web {
    position: absolute;
    left: 0; right: 0; top: 271px;
    text-align: center;
    color: var(--white);
    font-size: 18px;
    letter-spacing: 1.6px;
  }
</style>
</head>
<body>
  <section class="card card--front" aria-label="Card front">
    <div class="holder">
      <div class="holder__name">Daniel Hargrove</div>
      <div class="holder__title">Financial Advisor</div>
    </div>
    <div class="brand-name">STONEMARSH FINANCIAL LLC</div>
    <div class="rule rule--under"></div>
    <div class="rule rule--divider"></div>
    <div class="contact contact--left">
      <div class="contact__row"><span class="contact__label">Phone:</span><span>111-123-4567</span></div>
      <div class="contact__row"><span class="contact__label">Email:</span><span>info@stonemarshfinancial.com</span></div>
    </div>
    <div class="contact contact--right">
      <div class="contact__row"><span class="contact__label">Fax:</span><span>111-123-4567</span></div>
      <div class="contact__row"><span class="contact__label">Address:</span><span>XXX Some Street Address<br>State, Country</span></div>
    </div>
  </section>
  <div class="side-label side-label--front">Front</div>

  <section class="card card--back" aria-label="Card back">
    <div class="brand-name">STONEMARSH FINANCIAL LLC</div>
    <div class="rule rule--under"></div>
    <div class="web">www.stonemarshfinancial.com</div>
  </section>
  <div class="side-label side-label--back">Back</div>
</body>
</html>
```